Hörbuchcover
Zielgruppe
Spiritueller Hörbuchverlag für ganzheitliche Gesundheit, Glück und Wohlstand.
Aufgabenstellung
Benötigt wird ein schönes quadratisches Cover, 2400x2400 mindestens 72dpi für ein Hörbuchcover.
Auf dem Cover soll eine gelb/orange Rose zu in Form einer Blüte zu sehen sein.
Titel: Goldener Pfad
Untertitel: Gefühle öffnen die Tür zu mehr Heilung, Vitalität & Zuversicht
Autorenname: Dr. med. Katrin Wollberg
Das Velmira Logo soll unten mittig sitzen.
Es folgen weiterer Hörbücher von dieser Autorin und es wäre gut wenn man die folgenden Cover in einem ähnlichen Stil halten könnte. Ein harmonisches und gut zu erkennendes Design mit hohem Wiedererkennungseffekt. Ich freue mich auf kreative Designvorschläge.
Auf velmira.de kann man sehen wo das Logo sitzen soll.
Herzliche Grüße - Jonas

```html
<!DOCTYPE html>
<html lang="de">
<head>
<meta charset="utf-8">
<title>Goldener Pfad – Hörbuchcover</title>
<link rel="stylesheet" href="https://fonts.googleapis.com/css2?family=Cinzel:wght@400&family=Dancing+Script:wght@500&family=PT+Sans&display=swap">
<style>
  :root {
    --cream: #fbefd6;
    --honey: #f6d28f;
    --apricot: #f4b25e;
    --rose-core: #ec9338;
    --haze: #fff8ea;
    --plum: #5b1a3b;
    --white: #ffffff;
    --band: rgba(255, 250, 240, 0.55);
  }
  * { margin: 0; padding: 0; box-sizing: border-box; }
  html, body { width: 1200px; height: 1181px; overflow: hidden; }
  body { background: var(--cream); }

  .cover {
    position: relative;
    width: 1200px;
    height: 1181px;
    overflow: hidden;
  }

  .cover-artwork {
    position: absolute;
    inset: 0;
    background:
      radial-gradient(ellipse 420px 460px at 620px 760px, var(--rose-core) 0%, var(--apricot) 35%, rgba(246, 210, 143, 0) 75%),
      radial-gradient(ellipse 700px 380px at 600px 140px, var(--haze) 0%, rgba(255, 248, 234, 0) 80%),
      linear-gradient(180deg, var(--honey) 0%, var(--cream) 45%, var(--honey) 100%);
  }

  .author {
    position: absolute;
    top: 44px;
    width: 100%;
    text-align: center;
    font-family: "PT Sans", sans-serif;
    font-size: 30px;
    color: var(--plum);
    letter-spacing: 0.3px;
  }

  .title {
    position: absolute;
    top: 256px;
    width: 100%;
    text-align: center;
    font-family: "Cinzel", serif;
    font-weight: 400;
    font-size: 94px;
    line-height: 1.1;
    letter-spacing: 3px;
    color: var(--white);
    text-shadow: 0 0 3px rgba(91, 26, 59, 0.9), 0 2px 10px rgba(91, 26, 59, 0.45);
  }

  .subtitle-band {
    position: absolute;
    top: 523px;
    left: 0;
    width: 100%;
    height: 205px;
    background: var(--band);
    display: flex;
    flex-direction: column;
    justify-content: center;
    align-items: center;
  }

  .subtitle {
    font-family: "Dancing Script", cursive;
    font-weight: 500;
    font-size: 58px;
    line-height: 72px;
    color: var(--plum);
    text-align: center;
  }

  .publisher {
    position: absolute;
    top: 956px;
    width: 100%;
    display: flex;
    flex-direction: column;
    align-items: center;
    gap: 20px;
  }

  .publisher-dot {
    width: 66px;
    height: 66px;
    border-radius: 50%;
    background: var(--white);
  }

  .publisher-name {
    font-family: "PT Sans", sans-serif;
    font-size: 46px;
    letter-spacing: 8px;
    color: var(--white);
  }
</style>
</head>
<body>
  <main class="cover">
    <div class="cover-artwork" role="img" aria-label="Große gelb-orange Rosenblüte im Zentrum, umgeben von weißen Gänseblümchen in warmem, sonnigem Gegenlicht"></div>

    <p class="author">Dr. med. Katrin Wollberg</p>

    <h1 class="title">GOLDENER PFAD</h1>

    <div class="subtitle-band">
      <p class="subtitle">Gefühle öffnen die Tür zu mehr<br>Heilung, Vitalität &amp; Zuversicht</p>
    </div>

    <div class="publisher">
      <span class="publisher-dot"></span>
      <span class="publisher-name">VELMIRA</span>
    </div>
  </main>
</body>
</html>
```